Social Media Graphics - Oakline Push REVISED

Create 6-7 individual social media graphics (square size) to encourage folks to join our online course called:

The Harvest Ledger Circle
How to Launch a Multi-Million Business From Scratch
Sign Up Today!

IMPORTANT: Make the largest and most prominent text on the graphic be: How to Launch a Multi-Million Business From Scratch

For the color scheme of the graphics, let's try a blue color palette; make sure the graphics appeal to both men and women

Make sure each graphic contains 1 of the 3 pics attached (crop pic as needed); and make sure one of the graphics is all TEXT only.

Target Market(s)

men and women looking to start a business

Industry/Entity Type

Entrepreneurship

Colors
0054AA
0677BA
7BADD7
CADEEF
E8F1F8

Requirements
Must have
• All the text and use the 3 pics provided; one graphic can be all text; Simple, modern design that's easy to read

```html
<!DOCTYPE html>
<html lang="en">
<head>
<meta charset="utf-8">
<title>The Harvest Ledger Circle – Social Graphic</title>
<link rel="stylesheet" href="https://fonts.googleapis.com/css2?family=Montserrat:wght@600;700;800;900&family=Oswald:wght@700&display=swap">
<style>
  :root {
    --stage: #68a3c6;
    --blue-deep: #003a8c;
    --blue-mid: #0054aa;
    --blue-bright: #2b82d8;
    --navy: #0a1f66;
    --pink: #f2345e;
    --white: #ffffff;
  }
  * { margin: 0; padding: 0; box-sizing: border-box; }
  html, body {
    width: 1200px;
    height: 862px;
    overflow: hidden;
    background: var(--stage);
  }
  .post {
    position: absolute;
    left: 200px;
    top: 31px;
    width: 800px;
    height: 800px;
    overflow: hidden;
    background:
      radial-gradient(ellipse 60% 90% at 20% 30%, rgba(0, 30, 100, 0.45), transparent 70%),
      radial-gradient(ellipse 50% 70% at 75% 20%, rgba(90, 150, 230, 0.25), transparent 70%),
      linear-gradient(135deg, var(--blue-deep) 0%, var(--blue-mid) 45%, var(--blue-bright) 100%);
    color: var(--white);
  }
  .line {
    position: absolute;
    left: 0;
    right: 0;
    text-align: center;
    white-space: nowrap;
  }
  .title-top {
    top: 44px;
    font-family: "Montserrat", sans-serif;
    font-weight: 800;
    font-size: 92px;
    line-height: 1;
    letter-spacing: 1px;
  }
  .title-bottom {
    top: 168px;
    font-family: "Oswald", sans-serif;
    font-weight: 700;
    font-size: 66px;
    line-height: 1;
  }
  .megaphone {
    position: absolute;
    left: 594px;
    top: 227px;
    width: 155px;
    height: 170px;
    border-radius: 40% 50% 45% 30%;
    background: linear-gradient(150deg, #f2f5fa 0%, #9fb8d8 55%, #1f4fa0 100%);
  }
  .rays {
    position: absolute;
    left: 480px;
    top: 210px;
    width: 130px;
    height: 130px;
  }
  .frame {
    position: absolute;
    left: 96px;
    top: 356px;
    width: 611px;
    height: 120px;
    border: 3px solid var(--pink);
    border-bottom: none;
  }
  .tag {
    position: absolute;
    font-family: "Montserrat", sans-serif;
    font-weight: 600;
    line-height: 1;
    transform: rotate(-5deg);
    white-space: nowrap;
  }
  .tag-how {
    left: 237px;
    top: 293px;
    padding: 10px 16px 8px;
    background: var(--white);
    color: var(--blue-mid);
    font-size: 40px;
  }
  .tag-launch {
    left: 282px;
    top: 334px;
    padding: 10px 22px 8px;
    background: var(--pink);
    color: var(--white);
    font-size: 38px;
  }
  .headline-upper {
    top: 402px;
    font-family: "Oswald", sans-serif;
    font-weight: 700;
    font-size: 92px;
    line-height: 1;
  }
  .headline-main {
    top: 494px;
    font-family: "Montserrat", sans-serif;
    font-weight: 900;
    font-size: 124px;
    line-height: 1;
    color: var(--pink);
    letter-spacing: -2px;
  }
  .headline-sub {
    top: 619px;
    font-family: "Montserrat", sans-serif;
    font-weight: 700;
    font-size: 50px;
    line-height: 1;
  }
  .cta {
    position: absolute;
    left: 284px;
    top: 695px;
    width: 230px;
    height: 50px;
    border: 3px solid var(--white);
    border-radius: 25px;
    background: var(--navy);
    font-family: "Montserrat", sans-serif;
    font-weight: 700;
    font-size: 21px;
    line-height: 44px;
    text-align: center;
    letter-spacing: 0.5px;
  }
</style>
</head>
<body>
  <section class="post">
    <h1 class="line title-top">THE HARVEST</h1>
    <p class="line title-bottom">LEDGER CIRCLE</p>

    <svg class="rays" viewBox="0 0 130 130" aria-hidden="true">
      <line x1="12" y1="18" x2="60" y2="62" stroke="#0b1a40" stroke-width="4"/>
      <line x1="0" y1="78" x2="110" y2="104" stroke="#0b1a40" stroke-width="4"/>
    </svg>
    <div class="megaphone" role="img" aria-label="Megaphone illustration"></div>

    <div class="frame"></div>
    <span class="tag tag-how">HOW TO</span>
    <span class="tag tag-launch">LAUNCH A</span>

    <h2 class="line headline-upper">MULTI-MILLION</h2>
    <p class="line headline-main">BUSINESS</p>
    <p class="line headline-sub">FROM SCRATCH</p>

    <div class="cta">SIGN UP TODAY!</div>
  </section>
</body>
</html>
```